Verlindo Magician

I want the business card for my business to give to people who watch that later I will be employed to show magic here is my website http://www.balsamomagicien.com/I want the interesting design , i am very opened for formal and informal, I watch a lot of design so don't stick to the common shape and form but i hope it can also be produced the thing to write on will be the same as in picture that i will upload , i also will upload the logo for you that so can be easy to useDenis CostilleMagicianMAGICIAN BALSAMO 17 rue des Tilleuls - 25000 BESANÇON contact@verlindoillusions.example tel. 0381 946 157 tel. 0674 219 503

```html
<!DOCTYPE html>
<html lang="en">
<head>
<meta charset="utf-8">
<title>Verlindo Magician – Spade Business Card</title>
<link href="https://fonts.googleapis.com/css2?family=Jost:wght@300;400;700&family=Roboto+Condensed:wght@400;700&display=swap" rel="stylesheet">
<style>
  :root {
    --page: #ffffff;
    --card-front: #e8e9eb;
    --card-back: #cf3529;
    --ink: #111111;
    --paper: #ffffff;
    --rule: rgba(255,255,255,0.75);
  }
  html, body { margin: 0; padding: 0; overflow: hidden; background: var(--page); }
  .sheet { position: relative; width: 1200px; height: 1200px; overflow: hidden; background: var(--page); }
  .shapes { position: absolute; inset: 0; }
  .text { position: absolute; left: 0; width: 100%; text-align: center; margin: 0; line-height: 1; }
  .front .text { left: 160px; width: 400px; }
  .back .text { left: 640px; width: 400px; }

  .wordmark { font-family: "Jost", sans-serif; font-weight: 300; letter-spacing: 0.02em; }
  .front .wordmark { color: var(--ink); }
  .front .wordmark-name { top: 648px; font-size: 40px; }
  .front .wordmark-sub { top: 690px; font-size: 12px; letter-spacing: 0.06em; }
  .back .wordmark { color: var(--paper); }
  .back .wordmark-name { top: 466px; font-size: 47px; }
  .back .wordmark-sub { top: 516px; font-size: 15px; letter-spacing: 0.06em; }

  .rule { position: absolute; left: 690px; width: 302px; height: 1px; background: var(--rule); }
  .rule-top { top: 558px; }
  .rule-bottom { top: 622px; }

  .person-name { top: 566px; font-family: "Jost", sans-serif; font-weight: 700; font-size: 27px; color: var(--paper); }
  .person-role { top: 598px; font-family: "Jost", sans-serif; font-weight: 400; font-size: 16px; color: var(--paper); }

  .contact { font-family: "Roboto Condensed", sans-serif; color: var(--paper); font-size: 13.5px; }
  .company { top: 639px; font-weight: 700; font-size: 15px; }
  .address { top: 658px; }
  .email { top: 692px; }
  .phones { top: 710px; }
  .phones b { font-weight: 700; }

  .side-label { position: absolute; top: 904px; width: 200px; text-align: center; font-family: "Jost", sans-serif; font-weight: 700; font-size: 22px; color: var(--ink); margin: 0; }
  .label-front { left: 262px; }
  .label-back { left: 748px; }
</style>
</head>
<body>
<div class="sheet">
  <svg class="shapes" width="1200" height="1200" viewBox="0 0 1200 1200" xmlns="http://www.w3.org/2000/svg">
    <defs>
      <path id="spade-outline" d="M360 328 L560 524 C590 556 588 590 586 616 C584 700 520 766 456 764 C430 764 404 754 384 748 C386 810 400 850 444 878 L276 878 C320 850 334 810 336 748 C316 754 290 764 264 764 C200 766 136 700 134 616 C132 590 130 556 160 524 Z"/>
      <linearGradient id="portrait-tone" x1="0" y1="0" x2="0" y2="1">
        <stop offset="0" stop-color="#2a2a2a"/>
        <stop offset="1" stop-color="#0d0d0d"/>
      </linearGradient>
    </defs>
    <use href="#spade-outline" class="card-front" fill="var(--card-front)"/>
    <use href="#spade-outline" class="card-back" fill="var(--card-back)" transform="translate(480 0)"/>
    <rect class="portrait" x="268" y="416" width="184" height="228" rx="40" fill="url(#portrait-tone)" role="img" aria-label="Black ink illustration of the magician in a dark suit holding a playing card"/>
  </svg>

  <section class="front">
    <p class="text wordmark wordmark-name">VERLINDO</p>
    <p class="text wordmark wordmark-sub">MAGICIAN</p>
  </section>

  <section class="back">
    <p class="text wordmark wordmark-name">VERLINDO</p>
    <p class="text wordmark wordmark-sub">MAGICIAN</p>
    <div class="rule rule-top"></div>
    <p class="text person-name">Marc Ravoulet</p>
    <p class="text person-role">Magician</p>
    <div class="rule rule-bottom"></div>
    <p class="text contact company">MAGICIAN VERLINDO</p>
    <p class="text contact address">17 rue des Tilleuls - 25000 BESANÇON</p>
    <p class="text contact email">contact@verlindoillusions.example</p>
    <p class="text contact phones"><b>tel.</b> 0381 946 157 <b>tel.</b> 0674 219 503</p>
  </section>

  <p class="side-label label-front">front</p>
  <p class="side-label label-back">back</p>
</div>
</body>
</html>
```